Design for the A4 Letterhead, envelope and A4 Folder

Design have to be clean, professional, unique (eye catchy) and high end.
Colors: Yellow (Code: 803C), Darker Grey and Black or white (optional)
Logo can be in white or black

Letterhead:
Contain: 1. Korvane Logo
2. Slogan "MADE WITH PRIDE"
3. Company information:
Korvane Valves Pte. Ltd. (Singapore)
Registration no: 201947215K
Tel: (65) 6418 2904
Fax: (65) 6472 9186
Email: sales@korvanevalves.example
Website: http://www.korvanevalves.example
4. Logo watermark

Envelope:
Contain: 1. Korvane Logo
3. website: http://www.korvanevalves.example and email address:
sales@korvanevalves.example
4. Logo watermark

Folder:
Contain: 1. Korvane Logo
3. Company's information:
Tel: (65) 6418 2904
Fax: (65) 6472 9186
4. QR Code
5. Logo watermark
6. On the inside there is a space to insert business card. Contrast colors
between the inside and cover.
Updates

For the Folder design, please be informed that we would prefer to have the Korvane logo on the left hand side of the cover page, rather than on the right hand side.And also if we could highlight the "Made with Pride" slogan with either the yellow box or black/grey box depending on the background color.For the Envelope design,it does not matter where the position of the logo is. But please also highlight the "Made with Pride" Slogan For the Letterhead design, the position of the logo must be on the left hand side and the slogan must be highlighted. In addition, please include the following company information (only for the letterhead design)Korvane Valves Pte. Ltd. (Singapore)Registration no: 200308878MTel: (65) 6535 3735Fax: (65) 6533 3570Email: sales@dynatechpumps.comWebsite: http://www.korvanevalves.example Added Wednesday, August 2, 2017

Target Market(s)

Business to Business, High End market

Industry/Entity Type

It Professional

Font styles to use
Serif

Requirements
Must have
• Design have to be clean, professional, unique (eye catchy) and high end.
Nice to have
• color contrast but still maintaining the professionalism and the seriousness
Should not have
• Messy look, futuristic look, too crowded

```html
<!DOCTYPE html>
<html lang="en">
<head>
<meta charset="utf-8">
<title>Korvane Valves – Stationery</title>
<link href="https://fonts.googleapis.com/css2?family=PT+Sans:wght@400;700&family=Cookie&display=swap" rel="stylesheet">
<style>
  :root {
    --yellow: #ffff00;
    --grey-dark: #5a5a5a;
    --ink: #3c3c3c;
    --paper: #f4f4f2;
    --watermark: #eaeae8;
    --stage-top: #8c8c8c;
    --stage-bottom: #4a4a4a;
  }
  * { margin: 0; padding: 0; box-sizing: border-box; }
  html, body { width: 1200px; height: 754px; overflow: hidden; }
  body {
    position: relative;
    background: linear-gradient(180deg, var(--stage-top), var(--stage-bottom));
    font-family: "PT Sans", sans-serif;
    color: var(--ink);
  }
  .sheet {
    position: absolute;
    background: var(--paper);
    overflow: hidden;
    box-shadow: 0 2px 6px rgba(0,0,0,.35);
  }
  .watermark {
    position: absolute;
    border-radius: 50%;
    border: 34px solid var(--watermark);
  }
  .accent-bar { position: absolute; left: 0; width: 6px; background: var(--yellow); }
  .brand { position: absolute; text-align: center; }
  .brand-mark {
    display: block; margin: 0 auto;
    border-radius: 50%;
    border: 4px solid var(--grey-dark);
  }
  .brand-name {
    display: block;
    font-weight: 700;
    color: var(--grey-dark);
    letter-spacing: 1px;
    line-height: 1;
  }
  .slogan-band {
    position: absolute; left: 0; right: 0; height: 15px;
    background: var(--grey-dark);
  }
  .slogan-band .fill { position: absolute; left: 0; top: 0; bottom: 0; background: var(--yellow); }
  .slogan-text {
    position: absolute; top: -2px;
    font-family: "Cookie", cursive;
    font-size: 17px; line-height: 18px;
    color: var(--ink);
    transform: translateX(-50%);
    white-space: nowrap;
  }
  .slogan-mark {
    position: absolute; top: -3px; width: 20px; height: 20px;
    border-radius: 50%;
    background: var(--paper);
    border: 2px solid var(--grey-dark);
    transform: translateX(-50%);
  }

  /* Letterhead */
  .letterhead { left: 36px; top: 32px; width: 490px; height: 690px; }
  .letterhead .watermark { left: 192px; top: 356px; width: 440px; height: 440px; border-width: 40px; }
  .letterhead .accent-bar { top: 20px; height: 77px; }
  .letterhead .brand { left: 30px; top: 21px; width: 88px; }
  .letterhead .brand-mark { width: 48px; height: 48px; }
  .letterhead .brand-name { font-size: 19px; margin-top: 5px; }
  .contact {
    position: absolute; right: 36px; top: 20px;
    text-align: right; font-size: 8.5px; line-height: 11.2px;
  }
  .contact .icon { display: inline-block; width: 7px; height: 7px; margin-left: 4px; vertical-align: -1px; }
  .contact .plain { margin-right: 11px; }
  .letter { position: absolute; left: 37px; top: 193px; width: 424px; font-size: 7.2px; line-height: 11.7px; text-align: justify; }
  .salutation { font-size: 13.5px; line-height: 18px; margin-bottom: 22px; text-align: left; }
  .letter p { margin-bottom: 11.7px; }
  .closing { margin-top: 21px; }
  .signature { display: block; width: 64px; height: 24px; margin: 14px 0 0 9px; background: linear-gradient(90deg, #d6d6d4, #c4c4c2); border-radius: 2px; }
  .signatory { margin: 10px 0 0 12px; line-height: 1.1; }
  .signatory .name { font-size: 9px; letter-spacing: .3px; }
  .signatory .role { font-size: 7px; }
  .letterhead .slogan-band { top: 662px; }

  /* Envelope back */
  .envelope-back { left: 546px; top: 209px; width: 548px; height: 248px; }
  .envelope-back .watermark { left: 362px; top: 67px; width: 280px; height: 280px; border-width: 30px; }
  .flap { position: absolute; left: 0; top: 0; }
  .envelope-back .brand { left: 248px; top: 17px; width: 60px; }
  .envelope-back .brand-mark { width: 32px; height: 32px; border-width: 3px; }
  .envelope-back .brand-name { font-size: 13px; margin-top: 4px; }

  /* Envelope front */
  .envelope-front { left: 546px; top: 471px; width: 551px; height: 250px; }
  .envelope-front .accent-bar { top: 19px; height: 64px; }
  .envelope-front .brand { left: 20px; top: 20px; width: 66px; }
  .envelope-front .brand-mark { width: 38px; height: 38px; border-width: 3px; }
  .envelope-front .brand-name { font-size: 15px; margin-top: 3px; text-align: left; }
  .return-address { position: absolute; left: 22px; top: 82px; font-size: 7.2px; line-height: 9.9px; }
  .return-address .icon { display: inline-block; width: 7px; height: 7px; margin-right: 3px; vertical-align: -1px; }
  .envelope-front .slogan-band { top: 223px; }
</style>
</head>
<body>

<!-- Letterhead -->
<section class="sheet letterhead" aria-label="Letterhead">
  <div class="watermark"></div>
  <div class="accent-bar"></div>
  <div class="brand">
    <span class="brand-mark"></span>
    <span class="brand-name">KORVANE</span>
  </div>
  <address class="contact" style="font-style:normal">
    <div class="plain">Korvane Valves Pte. Ltd.</div>
    <div class="plain">42 Kestrel Lane #05-12</div>
    <div class="plain">Singapore 588110</div>
    <div>(65) 6418 2904<svg class="icon" viewBox="0 0 10 10"><path d="M2 0.5 L4 2.5 L3 4 Q4.5 6 6 7 L7.5 6 L9.5 8 L8 9.5 Q3.5 9 0.5 2 Z" fill="#555"/></svg></div>
    <div>(65) 6472 9186<svg class="icon" viewBox="0 0 10 10"><rect x="2.5" y="0.5" width="5" height="3" fill="#555"/><rect x="0.5" y="3.5" width="9" height="4.5" rx="1" fill="#555"/><rect x="2.5" y="7" width="5" height="2.5" fill="#777"/></svg></div>
    <div>sales@korvanevalves.example<svg class="icon" viewBox="0 0 10 10"><rect x="0.5" y="2" width="9" height="6.5" fill="#555"/><path d="M0.5 2 L5 6 L9.5 2" stroke="#ddd" fill="none"/></svg></div>
    <div>www.korvanevalves.example<svg class="icon" viewBox="0 0 10 10"><circle cx="5" cy="5" r="4.5" fill="#555"/><path d="M0.5 5 H9.5 M5 0.5 Q2 5 5 9.5 Q8 5 5 0.5" stroke="#ddd" stroke-width=".7" fill="none"/></svg></div>
  </address>

  <div class="letter">
    <p class="salutation">Dear Mr. Harlow,</p>
    <p>Lorem ipsum dolor sit amet, consectetur adipiscing elit. Donec orci purus, luctus vitae dignissim eu, iaculis sed purus. Vivamus faucibus, ipsum nec aliquet viverra, leo mauris condimentum ligula, sit amet sagittis enim ligula quis arcu. Nam egestas tortor id nisi porttitor mattis. In tortor ante, ultricies in suscipit a, tempus non massa. Vivamus et auctor mi. Fusce vel massa nulla. Phasellus nec eros mauris, et scelerisque orci.</p>
    <p>Donec malesuada orci vitae nulla accumsan porta a id massa. Quisque accumsan iaculis magna sit amet fringilla. Maecenas consequat, magna eget tincidunt semper, odio nibh rutrum mi, id feugiat ante nisi eu risus. Vestibulum nunc orci, rhoncus a placerat in, ultricies in mi. Cras mattis varius eros, vel fringilla nisi suscipit eget. Quisque scelerisque sagittis nulla at porttitor.</p>
    <p>Sed id augue vitae urna euismod commodo aliquet a quam. Pellentesque arcu velit, cursus et malesuada ut, consequat et diam. Nullam erat sem, rhoncus id ullamcorper vitae, rhoncus et arcu. In ultricies ultricies nulla, ut rutrum nisi iaculis at. Donec eu magna a metus ornare faucibus. Fusce aliquet faucibus ultricies. Morbi semper, est id tincidunt gravida, sem arcu adipiscing lacus, ac bibendum nulla leo eu purus. Quisque nec diam sed risus consectetur a ccumsan quis quis nibh. Vestibulum id purus lorem.</p>
    <p>It is a long established fact that a reader will be distracted by the readable content of a page when looking at its layout. The point of using Lorem Ipsum is that it has a more-or-less normal distribution of letters, as opposed to using 'Content here, content here', making it look like readable English. Many desktop publishing packages</p>
    <p class="closing">Sincerely,</p>
    <span class="signature" role="img" aria-label="Handwritten signature of Daniel Harlow"></span>
    <div class="signatory">
      <div class="name">DANIEL HARLOW</div>
      <div class="role">CEO/ Founder</div>
    </div>
  </div>

  <div class="slogan-band">
    <div class="fill" style="width:368px"></div>
    <span class="slogan-text" style="left:206px">Made With Pride</span>
    <span class="slogan-mark" style="left:368px"></span>
  </div>
</section>

<!-- Envelope back with flap -->
<section class="sheet envelope-back" aria-label="Envelope back">
  <div class="watermark"></div>
  <svg class="flap" width="548" height="92" viewBox="0 0 548 92" aria-hidden="true">
    <path d="M0 0 H548 L536 60 Q529 92 497 92 H51 Q19 92 12 60 Z" fill="var(--yellow)"/>
  </svg>
  <div class="brand">
    <span class="brand-mark"></span>
    <span class="brand-name">KORVANE</span>
  </div>
</section>

<!-- Envelope front -->
<section class="sheet envelope-front" aria-label="Envelope front">
  <div class="accent-bar"></div>
  <div class="brand">
    <span class="brand-mark"></span>
    <span class="brand-name">KORVANE</span>
  </div>
  <address class="return-address" style="font-style:normal">
    <div>Korvane Valves Pte. Ltd.</div>
    <div>42 Kestrel Lane #05-12</div>
    <div>Singapore 588110</div>
    <div><svg class="icon" viewBox="0 0 10 10"><path d="M2 0.5 L4 2.5 L3 4 Q4.5 6 6 7 L7.5 6 L9.5 8 L8 9.5 Q3.5 9 0.5 2 Z" fill="#555"/></svg>(65) 6418 2904</div>
    <div><svg class="icon" viewBox="0 0 10 10"><rect x="2.5" y="0.5" width="5" height="3" fill="#555"/><rect x="0.5" y="3.5" width="9" height="4.5" rx="1" fill="#555"/><rect x="2.5" y="7" width="5" height="2.5" fill="#777"/></svg>(65) 6472 9186</div>
  </address>
  <div class="slogan-band">
    <div class="fill" style="width:430px"></div>
    <span class="slogan-text" style="left:235px">Made With Pride</span>
    <span class="slogan-mark" style="left:430px"></span>
  </div>
</section>

</body>
</html>
```